Create an awesome website for a medical clinic

This is a new website for a doctor's office. The site should be clean and modern, easy to navigate.

This is a wellness clinic, we want to help our clients have a healthy, active lifestyle. It should be friendly and inviting, and easy for them to call or schedule an appointment.

The site should be responsive and designed using the attached Bootstrap 3 PSD.

We will provide stock photos, until then please use stock photos from:

pixelharbor.com or
framequarry.com (preferred)

Some example sites of clean and modern designs that we like:

https://tulsaspinecare.com/
http://reachpastjoints.com/
http://turninghealthier.com/

Also attached is a temporary logo you can use.

Reason: Thank you everyone for your great designs - we need a little more time so I'm extending the project.

Need extra days to review

Also, the colors in the new logo I just linked to are the final colors of the logo, so feel free to use any complimentary colors to it.

Hi everyone, The boss wants to change the layout of the site a little bit - here's the revised layout: https://www.filecrate.com/s/k9rt31vx2qp84zn/notes%2011_29_2017.pdf?dl=0 And the graphic assets you can use are here: https://www.filecrate.com/s/k9rt31vx2qp84zn/notes%2011_29_2017.pdf?dl=0 Feel free to change the background color of the "topbar", and change the icons of the "why people trust us" if you want, these are just temporary placeholders. Thanks for your patience and hard work!

Target Market(s)

People seeking medical treatment (wellness clinic)

Industry/Entity Type

Doctor

Number of Pages Required

1 page

Font styles to use
Sans Serif

Colors
0592cd
33a6d7
abd037
9bcb3c

Requirements
Must have
• The home page should have: a strong hero image/slideshow, clinic phone number should be prominent and at the top of the page (in the nav), a "what to expect" section (this is like a FAQs section - see attachment), and a strong call to action (a button to call or schedule an appointment).
• The what to expect section is useful so that prospective clients can determine if we're a good fit for them or not. It's a basic, first-step pre-qualification block of information.
• Social media icons which links to our social media profiles should be included.
Nice to have
• - Link to 3 most recent blog entries
• - Testimonials
• - How a multilevel nav menu looks.

```html
<!DOCTYPE html>
<html lang="en">
<head>
<meta charset="utf-8">
<title>Verdant Medical Clinic</title>
<link rel="stylesheet" href="https://fonts.googleapis.com/css2?family=Open+Sans:wght@400;600;700&family=Roboto+Condensed:wght@400;700&display=swap">
<style>
:root{
  --green:#1fa13c;
  --green-light:#8bc83c;
  --blue:#0592cd;
  --blue-light:#33a6d7;
  --grey-bg:#f2f2f2;
  --text:#444;
  --heading:#222;
  --footer:#1e1e1e;
  --white:#fff;
}
*{box-sizing:border-box;margin:0;padding:0}
html,body{width:1200px;height:3789px;overflow:hidden}
body{font-family:"Open Sans",Arial,sans-serif;color:var(--text);background:var(--white);position:relative}
h1,h2,h3,h4{font-family:"Roboto Condensed",Arial,sans-serif;font-weight:400;color:var(--heading)}
.section-title{font-size:30px;text-align:center;text-transform:uppercase;letter-spacing:.5px}
.btn{display:inline-block;background:var(--green);color:var(--white);font-size:13px;padding:8px 18px;border-radius:16px;text-decoration:none}

/* header */
.topbar{height:125px;position:relative}
.wordmark{position:absolute;left:90px;top:44px;display:flex;align-items:center;gap:12px;font-family:"Open Sans",Arial,sans-serif;font-weight:700;font-size:28px;color:var(--green);line-height:1;letter-spacing:.3px}
.wordmark .dot{width:22px;height:22px;border-radius:50%;background:var(--green)}
.phone{position:absolute;left:690px;top:38px;display:flex;gap:14px;align-items:center}
.phone .lbl{font-size:16px;color:#555;line-height:20px}
.appt{position:absolute;left:895px;top:42px;background:var(--blue-light);color:var(--white);font-size:14px;padding:10px 22px;border-radius:20px}
.nav{height:65px;background:linear-gradient(#9bcb3c,#7fb92f);display:flex;padding-left:100px}
.nav a{color:var(--white);font-size:16px;text-decoration:none;line-height:65px;padding:0 26px}
.nav a.active{background:var(--green)}

/* hero */
.hero{height:500px;position:relative;background:linear-gradient(120deg,#4d8a1f,#8dc447 45%,#5f9a2a 75%,#3f7618)}
.dropdown{position:absolute;left:503px;top:0;width:608px;height:300px;background:rgba(31,161,60,.95);display:grid;grid-template-columns:repeat(4,1fr);padding:18px 0 0 30px}
.dropdown ul{list-style:none}
.dropdown li{color:var(--white);font-size:14.5px;line-height:32.5px}
.dropdown li::before{content:"» ";font-weight:700}
.hero-title{position:absolute;left:588px;top:280px;font-size:36px;color:var(--white)}

/* welcome */
.welcome{height:435px;position:relative}
.welcome h2{position:absolute;left:108px;top:100px;font-size:30px}
.welcome p{position:absolute;left:108px;top:145px;width:478px;font-size:12.5px;line-height:22px}
.welcome .btn{position:absolute;left:108px;top:295px}
.video{position:absolute;left:630px;top:85px;width:462px;height:265px;border:4px solid #eee;background:linear-gradient(135deg,#d9e1ea,#9fb2c6 60%,#eef1f5)}
.video svg{position:absolute;left:201px;top:102px}

/* services */
.services{height:492px;background:linear-gradient(var(--blue),#0a86c5);color:var(--white);text-align:center;padding-top:88px}
.services h2{color:var(--white)}
.svc-row{display:flex;justify-content:center;gap:58px;margin-top:55px}
.svc{width:262px}
.svc .ic{width:104px;height:104px;border:2px solid var(--white);border-radius:50%;margin:0 auto;display:flex;align-items:center;justify-content:center}
.svc h3{color:var(--white);font-family:"Open Sans",Arial,sans-serif;font-size:22px;margin:24px 0 10px}
.svc p{font-size:13px;line-height:24px}
.svc .more{font-size:13px;margin-top:10px}

/* what we do */
.whatwedo{height:446px;background:var(--grey-bg);position:relative}
.ring{position:absolute;left:118px;top:85px;width:312px;height:282px}
.whatwedo h2{position:absolute;left:473px;top:112px;font-size:30px}
.whatwedo p{position:absolute;left:473px;top:158px;width:620px;font-size:12.5px;line-height:22px}
.whatwedo .btn{position:absolute;left:473px;top:335px}

/* expect */
.expect{height:452px;padding-top:95px}
.cards{display:flex;gap:54px;margin:60px 0 0 92px}
.card{width:330px;box-shadow:0 1px 5px rgba(0,0,0,.25);background:var(--white)}
.card .q{background:var(--blue);color:var(--white);font-size:13px;padding:0 12px;height:42px;display:flex;align-items:center;justify-content:space-between}
.card .a{padding:24px 14px 34px;font-size:13px;line-height:24px}

/* testimonial */
.testimonial{height:420px;background:linear-gradient(rgba(30,160,60,.9),rgba(30,160,60,.9)),linear-gradient(90deg,#3e7a2a,#9ac15a,#3e7a2a);text-align:center;padding-top:78px;color:var(--white)}
.testimonial h2{color:var(--white)}
.testimonial blockquote{width:750px;margin:25px auto 0;font-size:14px;line-height:22px}
.quote-mark{font-family:Georgia,serif;font-weight:700;font-size:22px}
.avatar-row{display:flex;justify-content:center;align-items:center;gap:40px;margin-top:28px}
.avatar{width:98px;height:98px;border-radius:50%;border:4px solid var(--white);background:linear-gradient(#8a5a44,#d9b49a)}
.testimonial .who{font-size:12px;font-style:italic;margin-top:16px}

/* blog */
.blog{height:550px;padding-top:95px}
.posts{display:flex;gap:27px;margin:58px 0 0 108px}
.post{width:312px;height:310px;box-shadow:0 1px 5px rgba(0,0,0,.2);text-align:center;position:relative}
.post .thumb{height:165px}
.post .date{position:absolute;left:76px;top:150px;width:160px;height:28px;line-height:28px;background:var(--blue-light);color:var(--white);font-size:12px}
.post h4{font-family:"Open Sans",Arial,sans-serif;font-size:15px;color:#333;margin-top:38px;letter-spacing:.3px}
.post p{font-size:11.5px;line-height:19px;margin:10px 22px 0;color:#666}
.post .more{font-size:11.5px;color:var(--green);margin-top:6px}

/* footer */
.footer{height:304px;background:var(--footer);color:#ddd;position:relative}
.footer .wordmark{left:113px;top:100px;font-size:24px}
.fcol{position:absolute;top:52px;font-size:12.5px}
.fcol h5{font-family:"Open Sans",Arial,sans-serif;font-weight:400;font-size:13.5px;color:var(--white);margin-bottom:20px;letter-spacing:.5px}
.contact li{list-style:none;display:flex;gap:12px;margin-bottom:8px}
.contact li span{line-height:18px}
.mail-form{display:flex;margin-top:14px}
.mail-form .field{width:142px;height:30px;background:var(--white);color:#999;font-size:11px;padding:8px}
.mail-form .go{background:var(--green);color:var(--white);font-size:12px;line-height:30px;padding:0 8px}
.social{list-style:none;display:grid;grid-template-columns:auto auto;gap:8px 18px}
.social a{color:#ddd;text-decoration:none;font-size:12.5px}
.social a::before{content:"› ";color:var(--green);font-weight:700}
.copy{position:absolute;left:90px;right:90px;top:237px;border-top:1px solid #333;text-align:center;padding-top:24px;font-size:12px}
</style>
</head>
<body>

<header class="topbar">
  <div class="wordmark"><span class="dot"></span>Verdant Medical Clinic</div>
  <div class="phone">
    <svg width="22" height="34" viewBox="0 0 22 34"><rect x="1" y="1" width="20" height="32" rx="3" fill="var(--green)"/><rect x="4" y="5" width="14" height="20" fill="#fff"/><circle cx="11" cy="29" r="2" fill="#fff"/></svg>
    <div class="lbl">Phone<br>(555) 014-2290</div>
  </div>
  <div class="appt">Schedule an Appointment</div>
</header>

<nav class="nav">
  <a href="#">Home</a><a href="#">About us</a><a href="#">Service</a><a href="#" class="active">Treatment</a><a href="#">Testimonials</a><a href="#">Blog</a><a href="#">Contacts</a>
</nav>

<section class="hero" role="img" aria-label="Smiling woman with raised arms standing in a sunny green meadow">
  <div class="dropdown">
    <ul><li>Quisquam</li><li>Dolorem</li><li>Neque</li><li>Ipsum</li><li>Consectetur</li><li>Porro est</li><li>Ipsum quia</li></ul>
    <ul><li>Dolorem</li><li>Neque</li><li>Consectetur</li><li>Porro est</li><li>Ipsum quia</li><li>Quisquam</li><li>Ipsum</li></ul>
    <ul><li>Quisquam</li><li>Dolorem</li><li>Neque</li><li>Ipsum</li><li>Consectetur</li><li>Porro est</li><li>Ipsum quia</li></ul>
    <ul><li>Dolorem</li><li>Neque</li><li>Consectetur</li><li>Porro est</li><li>Ipsum quia</li><li>Quisquam</li><li>Ipsum</li></ul>
  </div>
  <div class="hero-title">This is a wellness clinic</div>
</section>

<section class="welcome">
  <h2>WELCOME TO VERDANT</h2>
  <p>It is a long established fact that a reader will be distracted by the readable content of a page when looking at its layout. The point of using Lorem Ipsum is that it has a more-or-less normal distribution of letters, as opposed to using 'Content here, content here', making it look like readable English. Many desktop publishing packages and web page editors now use Lorem Ipsum as their default model text.</p>
  <a class="btn" href="#">Read More</a>
  <div class="video" role="img" aria-label="Video still of two doctors talking in a bright office">
    <svg width="60" height="60" viewBox="0 0 60 60"><circle cx="30" cy="30" r="29" fill="rgba(0,0,0,.55)"/><path d="M24 18 L42 30 L24 42Z" fill="#fff"/></svg>
  </div>
</section>

<section class="services">
  <h2 class="section-title">Our Services</h2>
  <div class="svc-row">
    <div class="svc">
      <div class="ic"><svg width="44" height="36" viewBox="0 0 44 36" fill="#fff"><circle cx="22" cy="9" r="7"/><path d="M10 34c0-9 5-14 12-14s12 5 12 14z"/><circle cx="8" cy="12" r="5"/><path d="M0 30c0-7 3-10 8-10 2 0 3 1 4 2-2 2-3 5-3 8z"/><circle cx="36" cy="12" r="5"/><path d="M44 30c0-7-3-10-8-10-2 0-3 1-4 2 2 2 3 5 3 8z"/></svg></div>
      <h3>Quisquam</h3><p>It is a long established fact that a reader will be distracted by the readable</p><div class="more">Learn More →</div>
    </div>
    <div class="svc">
      <div class="ic"><svg width="40" height="34" viewBox="0 0 40 34" fill="#fff"><path d="M14 4h12v4h-3V6h-6v2h-3z"/><rect x="2" y="8" width="36" height="24" rx="3"/><path d="M17 13h6v5h5v6h-5v5h-6v-5h-5v-6h5z" fill="var(--blue)"/></svg></div>
      <h3>Dolorem</h3><p>It is a long established fact that a reader will be distracted by the readable</p><div class="more">Learn More →</div>
    </div>
    <div class="svc">
      <div class="ic"><svg width="40" height="38" viewBox="0 0 40 38" fill="#fff"><path d="M20 0L40 9v3H0V9z"/><rect x="4" y="14" width="4" height="16"/><rect x="13" y="14" width="4" height="16"/><rect x="23" y="14" width="4" height="16"/><rect x="32" y="14" width="4" height="16"/><rect x="0" y="32" width="40" height="5"/></svg></div>
      <h3>Porro quisquam</h3><p>It is a long established fact that a reader will be distracted by the readable content</p><div class="more">Learn More →</div>
    </div>
  </div>
</section>

<section class="whatwedo">
  <svg class="ring" viewBox="0 0 312 282" role="img" aria-label="Portrait of a smiling female doctor in a white coat">
    <defs><linearGradient id="doc" x1="0" y1="0" x2="0" y2="1"><stop offset="0" stop-color="#e8eef2"/><stop offset="1" stop-color="#c9d6de"/></linearGradient></defs>
    <path d="M175 6 A138 138 0 1 0 175 276 A135 135 0 0 1 175 6Z" fill="var(--green)"/>
    <circle cx="180" cy="141" r="130" fill="url(#doc)"/>
  </svg>
  <h2>WHAT WE DO</h2>
  <p>It is a long established fact that a reader will be distracted by the readable content of a page when looking at its layout. The point of using Lorem Ipsum is that it has a more-or-less normal distribution of letters, as opposed to using 'Content here, content here', making it look like readable English. Many desktop publishing packages and web page editors now use Lorem Ipsum as their default model text, and a search for 'lorem ipsum' will uncover many web sites still in their infancy.</p>
  <a class="btn" href="#">Read More</a>
</section>

<section class="expect">
  <h2 class="section-title">What We Expect</h2>
  <div class="cards">
    <div class="card"><div class="q"><span><b>Q :</b> Neque porro quisquam est dolorem ?</span><svg width="14" height="14"><circle cx="7" cy="7" r="7" fill="#fff"/><path d="M4 6l3 3 3-3" stroke="var(--blue)" stroke-width="2" fill="none"/></svg></div>
      <div class="a"><b>A :</b> It is a long established fact that a reader will be distracted by the readable content of a page when looking at its layout.</div></div>
    <div class="card"><div class="q"><span><b>Q :</b> Dolorem ipsum quia dolor sit amet?</span><svg width="14" height="14"><circle cx="7" cy="7" r="7" fill="#fff"/><path d="M4 6l3 3 3-3" stroke="var(--blue)" stroke-width="2" fill="none"/></svg></div>
      <div class="a"><b>A :</b> It is a long established fact that a reader will be distracted by the readable content of a page when looking at its layout.</div></div>
    <div class="card"><div class="q"><span><b>Q :</b> Porro quisquam est qui dolorem ?</span><svg width="14" height="14"><circle cx="7" cy="7" r="7" fill="#fff"/><path d="M4 6l3 3 3-3" stroke="var(--blue)" stroke-width="2" fill="none"/></svg></div>
      <div class="a"><b>A :</b> It is a long established fact that a reader will be distracted by the readable content of a page when looking at its layout.</div></div>
  </div>
</section>

<section class="testimonial" aria-label="Testimonial">
  <h2 class="section-title">Testimonial</h2>
  <blockquote><span class="quote-mark">“</span> It is a long established fact that a reader will be distracted by the readable content of a page when looking at its layout. The point of using Lorem Ipsum is that it has a more-or-less normal distribution of letters, as opposed to using 'Content here, content here', making it look like readable English <span class="quote-mark">”</span></blockquote>
  <div class="avatar-row">
    <svg width="14" height="24"><path d="M12 2L3 12l9 10" stroke="#fff" stroke-width="3" fill="none"/></svg>
    <div class="avatar" role="img" aria-label="Portrait of the reviewing client"></div>
    <svg width="14" height="24"><path d="M2 2l9 10-9 10" stroke="#fff" stroke-width="3" fill="none"/></svg>
  </div>
  <div class="who">Mira Castellan</div>
</section>

<section class="blog">
  <h2 class="section-title">Latest Blog</h2>
  <div class="posts">
    <div class="post"><div class="thumb" role="img" aria-label="Woman jogging on a mountain trail" style="background:linear-gradient(#a9c3d6,#8a9a6a 60%,#5d7a3a)"></div><div class="date">14th May 2017</div>
      <h4>NEQUE PORRO QUISQUAM</h4><p>It has survived not only five centuries, but also the leap into electronic typesetting, remaining</p><div class="more">Read More »</div></div>
    <div class="post"><div class="thumb" role="img" aria-label="Woman with raised arms under a blue sky" style="background:linear-gradient(#3f8fd4,#8cc3ec)"></div><div class="date">14th May 2017</div>
      <h4>NEQUE PORRO QUISQUAM</h4><p>It has survived not only five centuries, but also the leap into electronic typesetting, remaining</p><div class="more">Read More »</div></div>
    <div class="post"><div class="thumb" role="img" aria-label="Smiling senior couple outdoors" style="background:linear-gradient(#d7dde0,#b89a86)"></div><div class="date">14th May 2017</div>
      <h4>NEQUE PORRO QUISQUAM</h4><p>It has survived not only five centuries, but also the leap into electronic typesetting, remaining</p><div class="more">Read More »</div></div>
  </div>
</section>

<footer class="footer">
  <div class="wordmark"><span class="dot"></span>Verdant Medical Clinic</div>
  <div class="fcol" style="left:417px">
    <h5>CONTACT US</h5>
    <ul class="contact">
      <li><svg width="10" height="14" viewBox="0 0 10 14"><path d="M5 0a5 5 0 0 1 5 5c0 4-5 9-5 9S0 9 0 5a5 5 0 0 1 5-5z" fill="#fff"/><circle cx="5" cy="5" r="2" fill="var(--footer)"/></svg><span>1820 Alder Lane<br>Brookfield 40512</span></li>
      <li><svg width="10" height="14" viewBox="0 0 10 14"><path d="M2 1l3 3-1 2 3 4 2-1 1 3-2 2C4 13 0 7 1 3z" fill="#fff"/></svg><span>555-017-4432</span></li>
      <li><svg width="12" height="10" viewBox="0 0 12 10"><rect width="12" height="10" fill="#fff"/><path d="M0 0l6 5 6-5" stroke="var(--footer)" fill="none"/></svg><span>hello@verdantclinic.example</span></li>
    </ul>
  </div>
  <div class="fcol" style="left:650px;width:220px">
    <h5>JOIN OUR MAILING LIST</h5>
    <div style="line-height:18px;font-size:11.5px">Your about us information would fit here nicely.</div>
    <div class="mail-form"><div class="field">Email address</div><div class="go">Submit</div></div>
  </div>
  <div class="fcol" style="left:950px">
    <h5>FOLLOW US OUT THERE</h5>
    <ul class="social">
      <li><a href="#">News</a></li><li><a href="#">Updates</a></li>
      <li><a href="#">Photos</a></li><li><a href="#">Videos</a></li>
    </ul>
  </div>
  <div class="copy">Copyright © 2017 All Rights Reserved</div>
</footer>

</body>
</html>
```